The Visual Personality of Miss Cobbler Food Trailer

Something that stands out with color and our logo. This is a food trailer that attends several events in the spring and summer. We are known for being one of the best Gumbo producers in mid Michigan. We have been responsible for connecting different communities and cultures together and we are strong supporters of our veterans since this is a veteran owned business. All of our vegetables are fresh and locally purchased. These recipes are originally from New Orleans Louisiana. Our website is Misscobbler.net. This will be used for an 8" x 11" poster. Leave a box or area that states "WHERE WE WILL BE:" so that we can add the location of the event that we are attending.

Target Market(s)

We do cuisine that is recognized in the southern states of the USA. but live in the northern part of the USA. We are providing a menu of different southern recipes so they do not have to go all the way down south for get..

Industry/Entity Type

Food/Restaurant Industry

Font styles to use
Serif
Decorative

Colors
0094D4
00A9DD
6FCCEA
C7EBF8
E9F6FB
59FF00
82FF00
B8FF75
E3FFCB
F4FFEA
FFF300
FFF600
FEFA6F
FFFEC7
FFFEE8
EE7325
F08F49
F5BC92
FAE3D3
FDF4ED
EB3D1F
EC4F4E
F09395
F8D3D4
FCEDEE
A7469A
B969AE
D3A5CF
EDDBEB
F8F0F9

Requirements
Must have
• Our logo, which is "Miss Cobbler", "Homemade Deliciousness". We need an area on the poster where we can manually add the location of the event we will be attending because it changes weekly. location
Nice to have
• Bold colors and logo

```html
<!DOCTYPE html>
<html lang="en">
<head>
<meta charset="utf-8">
<title>Miss Cobbler Food Trailer Poster</title>
<link rel="stylesheet" href="https://fonts.googleapis.com/css2?family=Bree+Serif&display=swap">
<style>
  :root {
    --paper: #f8f7f2;
    --ring-red: #e0101e;
    --hours-red: #c8102e;
    --ink: #222222;
    --body-brown: #4a3a30;
    --box-orange: #f7861f;
    --address-tint: #fba65a;
    --white: #ffffff;
    --star-yellow: #fcd54a;
  }
  * { margin: 0; padding: 0; box-sizing: border-box; }
  html, body { width: 848px; height: 1200px; overflow: hidden; background: var(--paper); }
  .poster {
    position: relative;
    width: 848px;
    height: 1200px;
    overflow: hidden;
    background: var(--paper);
    font-family: "Bree Serif", Georgia, serif;
    font-weight: 400;
  }
  h1, h2, p { font-weight: 400; }
  .ring, .photo, .deco { position: absolute; border-radius: 50%; }
  .ring { background: var(--ring-red); }
  .photo { border: 5px solid var(--white); }

  .ring--gumbo { left: -4px; top: -19px; width: 392px; height: 392px; }
  .photo--gumbo { left: -1px; top: 11px; width: 324px; height: 324px;
    background: radial-gradient(circle at 55% 45%, #d9663a 0%, #c4532c 45%, #b9b4a8 80%, #e8e4dc 100%); }

  .ring--flatbread { left: -3px; top: 559px; width: 172px; height: 172px; }
  .photo--flatbread { left: -4px; top: 573px; width: 144px; height: 144px;
    background: radial-gradient(circle at 50% 50%, #d9a56a 0%, #c7633f 50%, #cfc08a 100%); }

  .ring--poboy { left: 4px; top: 973px; width: 336px; height: 336px; }
  .photo--poboy { left: 15px; top: 1005px; width: 290px; height: 290px;
    background: linear-gradient(160deg, #e8d9b0 0%, #c98a44 40%, #d64a3a 65%, #e4e0cf 100%); }

  .ring--sandwich { left: 618px; top: 967px; width: 266px; height: 266px; }
  .photo--sandwich { left: 657px; top: 1010px; width: 212px; height: 212px;
    background: linear-gradient(170deg, #6b4a2e 0%, #c9853e 40%, #7a8a3e 65%, #3a2a1e 100%); }

  .brand {
    position: absolute;
    left: 446px;
    top: 70px;
    width: 400px;
    text-align: center;
  }
  .brand__mark {
    width: 110px; height: 110px;
    margin: 0 auto 20px;
    border-radius: 50%;
    background: var(--ring-red);
  }
  .brand__name {
    font-size: 50px;
    line-height: 1;
    color: var(--ink);
    letter-spacing: 2px;
  }
  .brand__tagline {
    margin-top: 12px;
    font-size: 15px;
    color: var(--ink);
    letter-spacing: 1.5px;
    text-transform: uppercase;
  }

  .deco--stars { border-radius: 6px; background: var(--star-yellow); opacity: 0.35; }
  .deco--stars-top { left: 390px; top: 280px; width: 66px; height: 58px; }
  .deco--stars-bottom { left: 392px; top: 1105px; width: 66px; height: 56px; }
  .deco--herb { left: 190px; top: 400px; width: 80px; height: 150px; border-radius: 40px;
    background: linear-gradient(200deg, #5fa83a, #3f8a2a); opacity: 0.55; transform: rotate(30deg); }
  .deco--chili { left: 82px; top: 806px; width: 168px; height: 76px; border-radius: 38px;
    background: linear-gradient(160deg, #e3463a 0%, #f29a4a 60%, #f6c27a 100%); opacity: 0.75; }
  .deco--bellpepper { left: 710px; top: 850px; width: 108px; height: 94px; border-radius: 45%;
    background: #8fcf4a; opacity: 0.55; }

  .mission {
    position: absolute;
    left: 307px;
    top: 472px;
    width: 468px;
    font-size: 15.5px;
    line-height: 33px;
    letter-spacing: 2.6px;
    text-transform: uppercase;
    color: var(--body-brown);
  }
  .mission__line {
    display: block;
    white-space: nowrap;
    text-align: justify;
    text-align-last: justify;
  }
  .mission__line--last { text-align-last: left; }

  .location-box {
    position: absolute;
    left: 272px;
    top: 698px;
    width: 538px;
    height: 202px;
    border-radius: 26px;
    background: var(--box-orange);
  }
  .location-box__label {
    position: absolute;
    left: 30px;
    top: 43px;
    font-size: 22px;
    letter-spacing: 0.8px;
    color: var(--white);
  }
  .location-box__address {
    position: absolute;
    left: 0; right: 0;
    top: 103px;
    text-align: center;
    font-size: 22px;
    letter-spacing: 3px;
    color: var(--address-tint);
  }

  .hours {
    position: absolute;
    left: 243px;
    top: 940px;
    width: 480px;
    text-align: center;
    font-size: 26px;
    line-height: 38px;
    color: var(--hours-red);
  }
</style>
</head>
<body>
<main class="poster">
  <div class="ring ring--gumbo"></div>
  <div class="photo photo--gumbo" role="img" aria-label="Bowl of gumbo with tomatoes, peppers and rice"></div>

  <div class="ring ring--flatbread"></div>
  <div class="photo photo--flatbread" role="img" aria-label="Flatbread topped with shrimp, tomato and herbs"></div>

  <div class="ring ring--poboy"></div>
  <div class="photo photo--poboy" role="img" aria-label="Po'boy sandwich with tomato and slaw beside chips"></div>

  <div class="ring ring--sandwich"></div>
  <div class="photo photo--sandwich" role="img" aria-label="Stacked club sandwich with fries"></div>

  <header class="brand">
    <div class="brand__mark"></div>
    <h1 class="brand__name">Miss Cobbler</h1>
    <p class="brand__tagline">Fresh From The Bayou!</p>
  </header>

  <div class="deco deco--stars deco--stars-top" role="img" aria-label="Small yellow sparkle accents"></div>
  <div class="deco deco--herb" role="img" aria-label="Sprigs of fresh cilantro"></div>
  <div class="deco deco--chili" role="img" aria-label="Red and orange chili peppers"></div>
  <div class="deco deco--bellpepper" role="img" aria-label="Green bell pepper rings"></div>

  <p class="mission">
    <span class="mission__line">We prepare and serve amazing</span>
    <span class="mission__line">high quality, delicious southern</span>
    <span class="mission__line">food at an affordable price. We</span>
    <span class="mission__line">want to provide our customers</span>
    <span class="mission__line">with the most authentic Louisiana</span>
    <span class="mission__line mission__line--last">experience outside of Louisiana.</span>
  </p>

  <section class="location-box">
    <h2 class="location-box__label">WHERE WE WILL BE</h2>
    <p class="location-box__address">YOUR ADDRESS HERE</p>
  </section>

  <div class="hours">
    <p>Monday, Friday, Saturday</p>
    <p>11:00 am EST - 3 pm EST</p>
    <p>www.misscobbler.net</p>
  </div>

  <div class="deco deco--stars deco--stars-bottom" role="img" aria-label="Small yellow sparkle accents"></div>
</main>
</body>
</html>
```